Penny Harvest

Logo and general packaging design for premium quality, price conscious super foods.

Initial product portfolio includes:

Organic Raw Chia Seeds - Resealable plastic bags with 3 x 5 label.
Organic Cold Pressed Coconut Oil (plastic jar) - 2.5 x 6.5 label

The design should be transferable to additional products.

Project requirements:

The design should be simple and the core trade dress should be no more than 2 or 3 colors. The logo should reproduce well in black/1 color.

The idea of this design is to convey quality and simplicity, like a "no frills", premium quality brand.

Deliverable: fully editable (text and illustration):

Logo.

Basic Jar label design.

Basic Bag label design.

Target Market(s)

Educated women aged 22-45

Industry/Entity Type

Plastic

Requirements
Must have
• Clear, simple logo, delivered in vector form, 1 color/black.
• Use of logo on 1 jar label and 1 bag label, each with product name and space for required and optional marketing content.
Nice to have
• Additional iterations of the design to demonstrate your concept of how we will visually vary additional items in jars and bags.
• i.e. What an additional product in a bag would look like for purposes of brand consistency and product differentiation on shelf or online in e-store.
Should not have
• overly detailed graphics that don't scale well and/or may be hard to read or understand. 4 color design elements (except to simiulate how the product may look through the clear jar or bag or how the product may be placed in a simulated surrounding or ad.

```html
<!DOCTYPE html>
<html lang="en">
<head>
<meta charset="utf-8">
<title>Penny Harvest – Organic Raw Chia Seeds Label</title>
<link rel="stylesheet" href="https://fonts.googleapis.com/css2?family=Oswald:wght@500&family=Zilla+Slab:wght@700&family=Arimo:wght@700&display=swap">
<style>
  :root {
    --ink: #2a2116;
    --taupe: #857563;
    --paper: #ffffff;
    --plant-light: #4a3f33;
  }
  * { margin: 0; padding: 0; box-sizing: border-box; }
  html, body { width: 1200px; height: 721px; overflow: hidden; background: var(--taupe); }
  .label {
    position: relative;
    width: 1200px;
    height: 721px;
    background: var(--taupe);
    font-family: "Arimo", Arial, sans-serif;
    overflow: hidden;
  }
  .side-panel {
    position: absolute;
    left: 0; top: 0;
    width: 402px; height: 721px;
    background: var(--ink);
    border-right: 3px dotted var(--ink);
  }
  .plant-art {
    position: absolute;
    left: 64px; top: 40px;
    width: 320px; height: 681px;
    background: linear-gradient(180deg, var(--ink) 0%, var(--plant-light) 45%, var(--ink) 100%);
  }
  .natural-badge {
    position: absolute;
    left: 35px; top: 547px;
    width: 128px; height: 128px;
    border-radius: 50%;
    background: var(--taupe);
    color: var(--paper);
    display: flex; flex-direction: column;
    align-items: center; justify-content: center;
    font-weight: 700;
    line-height: 1.05;
  }
  .natural-badge .pct { font-size: 27px; }
  .natural-badge .word { font-size: 25px; }
  .brand-name {
    position: absolute;
    left: 402px; right: 0; top: 66px;
    text-align: center;
    font-family: "Oswald", "Arial Narrow", sans-serif;
    font-weight: 500;
    font-size: 44px;
    letter-spacing: 1px;
    color: var(--ink);
  }
  .product-title {
    position: absolute;
    left: 402px; right: 0; top: 190px;
    text-align: center;
    font-family: "Zilla Slab", Georgia, serif;
    font-weight: 700;
    color: var(--paper);
    line-height: 1;
  }
  .product-title .line-organic { display: block; font-size: 128px; letter-spacing: 4px; }
  .product-title .line-name { display: block; font-size: 62px; letter-spacing: 2px; margin-top: 6px; }
  .title-divider {
    position: absolute;
    left: 733px; top: 377px;
    width: 118px; height: 4px;
    background: var(--paper);
    border-radius: 2px;
  }
  .benefits {
    position: absolute;
    left: 402px; right: 0; top: 397px;
    text-align: center;
    font-size: 21px;
    letter-spacing: 1px;
    color: var(--paper);
  }
  .net-weight {
    position: absolute;
    left: 402px; right: 0; top: 488px;
    text-align: center;
    font-size: 18px;
    color: var(--paper);
  }
  .marketer, .dates {
    position: absolute;
    top: 646px;
    font-size: 17px;
    line-height: 26px;
    color: var(--ink);
  }
  .marketer { left: 460px; }
  .dates { left: 768px; }
</style>
</head>
<body>
  <main class="label">
    <div class="side-panel">
      <div class="plant-art" role="img" aria-label="White botanical illustration of flowering chia plant stems"></div>
      <div class="natural-badge">
        <span class="pct">100%</span>
        <span class="word">natural</span>
      </div>
    </div>

    <div class="brand-name">PENNY HARVEST</div>

    <h1 class="product-title">
      <span class="line-organic">ORGANIC</span>
      <span class="line-name">RAW CHIA SEEDS</span>
    </h1>
    <div class="title-divider" role="img" aria-label="Decorative flourish divider"></div>

    <p class="benefits">ANTIOXIDANTS | CALCIUM | OMEGA FATTY ACIDS</p>
    <p class="net-weight">Net Weight 100gms</p>

    <p class="marketer">Marketed by: Penny Harvest<br>12 Mill Lane, Ashford, 40217</p>
    <p class="dates">Date of packing:<br>Expiry date:</p>
  </main>
</body>
</html>
```